Systems and Technology Consultants - Website

Design & Build a website for a new company which operates in the Systems and Technology space for Transportation, Government and Commercial sectors.

Overall design should be minimalist in nature.
Should also have a feed that provides news and event updates on the main page.
Logo has already been awarded and should be incorporated into the site.

We like the overall layout, functionality and simplicity of the below sites. Submitted designs could be similar to or a combination of the aspects on these sites, or perhaps a whole different concept - we are open to new ideas.
Norvique.com
Teblo.it

Update 1 Dated 27 May 2014

All I am moving away from the Teblo.it website and would like it to be more aligned with Norvique.com not only in layout but in functionality. I will be extending the deadline of this design brief for two weeks to incorporate additional requirements and will add addtional funding to the project.

Apologies for not having more information available to provide but with so many submissions its getting confusing.

Thanks Derek

Please note that the brief has been updated and the deadline has been extended.

Important: We will need two language versions of the website, English and Arabic; the website is hosted on HostPelican

Hello All, Thank you for your submissions. We have narrowed it down to the final 6 designers and I just wanted to take a moment and provide a bit of feedback regarding the concepts that we like and the modifications we are looking for. First, let me mention some of the design functions we like. - At the top of the homepage we really like the "region" or "language" tab so that the website can be viewed in both English and Arabic. - We like the homepage to have clear color variation so that the different sections of the homepage are distinct. Additionally, we like the bottom portion of the homepage to be in red. We feel that draws attention to our contact information. Again, we would like the colors to integrate black, gray-scale, red, etc. - Having a search tab at the top of the home page, or integrated into the main image, so that the site is easy to navigate. - We especially like the main image to have the scrolling tabs at the bottom so it is easy to browse the services offered (Consultancy, Solutions Architecture, Masters Systems Integration, Independent Design Review). - In regards to the services offered tab we really like the idea that a few people presented that have the outside of our logo with an icon in the middle of consultancy, solutions, etc., etc. Secondly, as mentioned in our brief we really enjoy the design of norvique site. Specially, we enjoy the strong iconic images they use, the way the tabs at the top scroll easily, and contact us page that generates an email. Lastly, I've included some photos of the concept we have been working on. What we are trying to demonstrate is how our company offers a range of services that are essentially linked together. We provide individual services that when combined present the full service package. We would like this concept to be integrated into the over concept of our website. Please feel free to ask for clarification of any of the above points or contact us if you have any additional questions. We appreciate all of your hard work and are very excited to see the updated designs. Best, Marta Vennick Quelbrant Senior Program Manager marta.vennick@quelbrant-example.com

Industry/Entity Type

Government

Font styles to use
Serif
Sans Serif

Requirements
Must have
• Must work on/adapt to various/mobile devices (responsive)
Must be simple and straightforward
Colors should be in line/matching with logo
2 language versions: English and Arabic (no Thai)
Services should be the first group/row of items after/below the main image
Note: the website will be hosted by hostpelican
Nice to have
• Submit feedback form
What's New section
The banner at the bottom of the site should not be too large; we would like a narrow one more
It would be nice if the header/top banner (with Home, About, etc. tabs) could stay in place as you scroll down (like Norvique and plain circle)
We will likely only use one image with a Company slogan on the Home page rather than a carousel of images to rotate through
Should not have
• This is the existing website: http://www.quelbrant-example.org
We do not like the animation, the way the banner icons/titles bounce
Not simple enough, we don't like the functionality or how pages load so slowly
We do not like the logo centered - it should be at the left
The banner and its tabs should not be towards the right, we would like them to be centered, to go all the way across and to be below the logo

```html
<!DOCTYPE html>
<html lang="en">
<head>
<meta charset="utf-8">
<title>Quelbrant International</title>
<link href="https://fonts.googleapis.com/css2?family=Open+Sans:wght@300;400;600;700&display=swap" rel="stylesheet">
<style>
:root{
  --red:#e8232b;
  --red-light:#f0474e;
  --ink:#1e1e1e;
  --text:#555;
  --page:#fafafa;
  --footer:#efefef;
  --muted:#666;
}
*{margin:0;padding:0;box-sizing:border-box}
html,body{width:783px;height:1200px;overflow:hidden}
body{background:var(--page);font-family:"Open Sans",sans-serif;color:var(--text);position:relative}
.abs{position:absolute}
.brand{left:109px;top:56px;display:flex;align-items:center;gap:8px}
.brand-mark{width:18px;height:18px;background:var(--red)}
.brand-name{color:var(--ink);font-weight:600;font-size:13px;line-height:1}
.nav{left:109px;top:109px;width:565px;height:38px;background:var(--red);display:flex;align-items:center}
.nav a{color:#fff;font-size:8.6px;font-weight:700;text-decoration:none;padding:0 7px;line-height:38px}
.nav a.active{background:var(--red-light);padding:0 12px}
.search{left:492px;top:118px;width:174px;height:19px;background:var(--red-light);color:#fff;font-size:7px;font-weight:600;padding:2px 0 0 9px;line-height:15px}
.hero{left:109px;top:146px;width:565px;height:244px;background:linear-gradient(90deg,#fbfbfb 0%,#eef0f2 40%,#c9d7e6 75%,#9fb8d6 100%);border:1px solid #e2e2e2}
.hero-title{left:142px;top:240px;color:var(--red);font-weight:700;font-size:37px;line-height:1}
.hero-sub{left:142px;top:279px;color:#444;font-weight:700;font-size:21px;line-height:1}
.dots{left:125px;top:365px;display:flex;gap:4px}
.dots span{width:10px;height:10px;border-radius:50%;background:#444}
.dots span.on{background:var(--red)}
.section-title{color:var(--red);font-weight:700;font-size:14.5px}
.services-title{left:0;width:783px;text-align:center;top:409px}
.service{top:439px;width:134px}
.service .photo{height:82px;width:132px}
.service h3{font-size:9.6px;color:var(--ink);font-weight:700;margin:15px 0 9px}
.service p{font-size:8px;line-height:14.4px;font-weight:300;color:#444}
.btn{display:inline-block;background:var(--red);color:#fff;font-weight:700;font-size:8px;text-decoration:none}
.service .btn{margin-top:14px;padding:2px 4px;line-height:13px}
.welcome-photo{left:109px;top:696px;width:277px;height:146px;background:linear-gradient(180deg,#3f86d4,#8ebde8 60%,#dfe9f3)}
.welcome-title{left:109px;top:851px;font-size:15px}
.welcome-text{left:109px;top:887px;width:280px;font-size:8.1px;line-height:14.4px;font-weight:300;color:#444}
.welcome-text p+p{margin-top:14.4px}
.btn-lg{padding:0;width:71px;height:27px;line-height:27px;text-align:center;font-size:8.3px}
.news-title{left:398px;top:692px}
.news{left:398px;width:278px;display:flex;gap:6px}
.news .thumb{width:85px;height:64px;flex:none}
.news-body{font-size:8.1px;line-height:14.4px;width:184px;font-weight:300;color:#444}
.news-body strong{display:block;color:#333;font-weight:700;margin-top:-3px}
.news-body .meta{color:#222;font-size:7.2px;font-weight:400}
.footer{left:0;top:1142px;width:783px;height:58px;background:var(--footer)}
.footer-links{left:102px;top:1155px;font-size:8px;color:var(--muted)}
.footer-links span{margin:0 8px}
.copy{left:102px;top:1175px;font-size:7.8px;color:var(--muted)}
.social{top:1153px;width:31px;height:31px;border-radius:50%}
</style>
</head>
<body>
<div class="abs brand"><span class="brand-mark"></span><span class="brand-name">Quelbrant International</span></div>

<nav class="abs nav">
  <a class="active" href="#">Home</a><a href="#">Business Units</a><a href="#">Services</a><a href="#">About Us</a><a href="#">Locations</a><a href="#">Contact Us</a>
</nav>
<div class="abs search">Search</div>

<div class="abs hero" role="img" aria-label="Three smiling engineers in hard hats holding rolled plans in a bright office"></div>
<div class="abs hero-title">System</div>
<div class="abs hero-sub">Professionals</div>
<div class="abs dots"><span class="on"></span><span></span><span></span><span></span></div>

<h2 class="abs section-title services-title">Services</h2>

<div class="abs service" style="left:109px">
  <div class="photo" role="img" aria-label="Engineer in safety vest at a laptop" style="background:linear-gradient(90deg,#c8ccd2,#e4e6ea 55%,#d9874a)"></div>
  <h3 style="margin-top:11px">Consulting</h3>
  <p>Lorem Ipsum is simply dummy text of the printing and typesetting industry. Lorem Ipsum has been the industry's standard dummy text ever since the 1500s</p>
  <a class="btn" href="#">Read More</a>
</div>
<div class="abs service" style="left:253px">
  <div class="photo" role="img" aria-label="Business team reviewing documents" style="background:linear-gradient(90deg,#e9e2da,#cfc9c4 50%,#6e6660)"></div>
  <h3>Engineering</h3>
  <p>Lorem Ipsum is simply dummy text of the printing and typesetting industry. Lorem Ipsum has been the industry's standard dummy text ever since the 1500s</p>
  <a class="btn" href="#">Read More</a>
</div>
<div class="abs service" style="left:398px">
  <div class="photo" role="img" aria-label="Construction worker holding a yellow hard hat" style="background:linear-gradient(135deg,#3a3a3c,#6b6d70 50%,#2b2b2d)"></div>
  <h3>Construction</h3>
  <p>Lorem Ipsum is simply dummy text of the printing and typesetting industry. Lorem Ipsum has been the industry's standard dummy text ever since the 1500s</p>
  <a class="btn" href="#">Read More</a>
</div>
<div class="abs service" style="left:542px">
  <div class="photo" role="img" aria-label="Operations diagram sketched on glass" style="background:linear-gradient(135deg,#cfdcda,#aebfbd 55%,#e3ebea)"></div>
  <h3>Operations</h3>
  <p>Lorem Ipsum is simply dummy text of the printing and typesetting industry. Lorem Ipsum has been the industry's standard dummy text ever since the 1500s</p>
  <a class="btn" href="#">Read More</a>
</div>

<div class="abs welcome-photo" role="img" aria-label="Engineer in a hard hat studying a blueprint against blue sky"></div>
<h2 class="abs section-title welcome-title">Welcome to Quelbrant International</h2>
<div class="abs welcome-text">
  <p>Quelbrant specializes in delivering quality professional services and technical projects that support larger business goals.  systems are tools that support a greater business function and need. we understand that most technical projects are conceptualized to support a larger vision with actual business goals in mind and ensure that all of our professional and certified expertise is included in our professional services to meet those goals.</p>
  <p>quelbrant recognizes the middle east and greater asia regions are economic growth markets with developing infrastructure projects requiring specialist systems and technical expertise.  accordingly, quelbrant has evolved its presence in the regions to meet client demands and expectations.</p>
</div>
<a class="abs btn btn-lg" href="#" style="left:110px;top:1078px">Read More</a>

<h2 class="abs section-title news-title">News &amp; Events</h2>
<div class="abs news" style="top:726px">
  <div class="thumb" role="img" aria-label="Surveyor at a yellow survey instrument" style="background:linear-gradient(90deg,#c9a32a,#e8d26a 50%,#8fb0cf)"></div>
  <div class="news-body"><strong>Lorem Ipsum is simply dummy text of the printing and typesetting industry.</strong> Lorem Ipsum has been the industry's standard dummy text ever since the 1500s, when an unknown printer took a galley of type and scrambled it to make a type specimen book.<div class="meta">Posted &nbsp;on May 16th 2014 &nbsp;By Admin</div></div>
</div>
<div class="abs news" style="top:842px">
  <div class="thumb" role="img" aria-label="Group of colleagues at a meeting" style="background:linear-gradient(90deg,#7d8fa6,#c4ccd6 50%,#5e6f86)"></div>
  <div class="news-body"><strong>Lorem Ipsum is simply dummy text of the printing and typesetting industry.</strong> Lorem Ipsum has been the industry's standard dummy text ever since the 1500s, when an unknown printer took a galley of type and scrambled it to make a type specimen book.<div class="meta">Posted &nbsp;on May 16th 2014 &nbsp;By Admin</div></div>
</div>
<div class="abs news" style="top:964px">
  <div class="thumb" role="img" aria-label="Team reviewing plans on a desk" style="background:linear-gradient(90deg,#dfe4ea,#b7c2cf 55%,#3b4a5e)"></div>
  <div class="news-body"><strong>Lorem Ipsum is simply dummy text of the printing and typesetting industry.</strong> Lorem Ipsum has been the industry's standard dummy text ever since the 1500s, when an unknown printer took a galley of type and scrambled it to make a type specimen book.<div class="meta">Posted &nbsp;on May 16th 2014 &nbsp;By Admin</div></div>
</div>
<a class="abs btn btn-lg" href="#" style="left:602px;top:1078px;width:72px">Read More</a>

<footer class="abs footer"></footer>
<div class="abs footer-links">Home<span>|</span>Business Units<span>|</span>Services<span>|</span>About Us<span>|</span>Locations<span>|</span>Contact Us</div>
<div class="abs copy">© 2014 Company Name,All Rights reserved</div>
<div class="abs social" role="img" aria-label="Social link" style="left:609px;background:#4fb8d6"></div>
<div class="abs social" role="img" aria-label="Social link" style="left:643px;background:#3a5a98"></div>
</body>
</html>
```